WordPress website design for wealth management company

A modern clean look website for a service company. This is mostly for information only, with a form to capture prospect contact information and schedule a 15 minutes call. There will be several static pages describe what services we offer, how we are different, and a blog section for posting articles and share resources. A section for client testimonials.
I want a website that is easy to understand and maintain. No proprietary plugins that cost extra. The main thing I need help is the visual layout / color palette that present a clean and professional look, select the suitable stock photos that convey the image of trust, professional, innovative, and high service.
Some websites with style I like include the following
- https://www.halvorbrook.com/
- https://www.trivanplanningworks.com/
- https://morvellfunds.com/private-equity-partners/
Also some websites in other industries with clean modern look
- https://zentrell.com/
- https://quovra.com/
- https://www.plumtorvik.com/
I want the end product to be a fully functional website that I can upload into web hosting service I use and I can easily add content and maintain myself in the future.

```html
<!DOCTYPE html>
<html lang="en">
<head>
<meta charset="utf-8">
<meta name="format-detection" content="telephone=no">
<title>Brenlow Wealth</title>
<link href="https://fonts.googleapis.com/css2?family=Jost:wght@500;600;700&family=Poppins:wght@300;400;500;600&display=swap" rel="stylesheet">
<style>
:root{
  --purple:#582585;
  --purple-deep:#4a1f73;
  --purple-light:#7a4bb0;
  --ink:#111111;
  --text:#3d3d3d;
  --grey-bg:#f2f2f2;
  --white:#ffffff;
  --gold:#e3a02b;
}
*{margin:0;padding:0;box-sizing:border-box}
html,body{width:1200px;height:4364px;overflow:hidden}
body{position:relative;background:var(--white);font-family:"Poppins",sans-serif;color:var(--text)}
a{color:inherit;text-decoration:none}
.abs{position:absolute}
.heading{font-family:"Jost",sans-serif;font-weight:600;color:var(--purple);letter-spacing:.5px;text-transform:uppercase}
.body-copy{font-weight:300;font-size:16.5px;line-height:30px;color:var(--text)}

/* nav */
.site-nav{left:0;top:0;width:1200px;height:77px;background:var(--white)}
.brand{left:120px;top:20px;display:flex;align-items:center;gap:8px;font-family:"Poppins",sans-serif;font-weight:600;font-size:15px;color:var(--purple);letter-spacing:1px}
.brand-dot{width:16px;height:16px;border-radius:50%;background:var(--gold)}
.nav-link{top:30px;font-family:"Poppins",sans-serif;font-weight:600;font-size:16px;color:var(--purple);letter-spacing:.5px}

/* hero */
.hero{left:0;top:77px;width:1200px;height:523px;background:linear-gradient(90deg,#c9c3cf 0%,#8d7aa6 30%,#6a3a9c 50%,var(--purple) 100%)}
.hero-photo{left:0;top:77px;width:560px;height:523px;background:linear-gradient(90deg,#b8b2bd,#9c8fae 60%,rgba(106,58,156,0))}
.hero-title{left:596px;top:184px;font-family:"Jost",sans-serif;font-weight:700;font-size:64px;line-height:76px;color:var(--white);letter-spacing:1px}
.hero-copy{left:602px;top:357px;width:434px;font-weight:300;font-size:17px;line-height:30px;color:var(--white);text-align:justify}

/* about */
.about-photo{left:112px;top:707px;width:407px;height:407px;background:radial-gradient(circle at 50% 50%,#d6e7ea,#9ccbd3 70%)}
.about-title{left:600px;top:697px;font-size:40px}
.about-copy{left:600px;top:780px;width:490px;text-align:justify}
.btn{background:var(--purple);color:var(--white);font-family:"Poppins",sans-serif;font-weight:600;font-size:15px;display:flex;align-items:center;justify-content:center;letter-spacing:.3px}
.about-btn{left:600px;top:1068px;width:158px;height:47px}

/* services */
.services{left:0;top:1215px;width:1200px;height:805px;background:var(--grey-bg)}
.services-title{left:112px;top:1312px;font-size:40px}
.services-copy{left:114px;top:1390px;width:820px}
.service-card{top:1553px;width:249px;height:349px;box-shadow:0 4px 12px rgba(0,0,0,.18);background:linear-gradient(180deg,#c7ccd2 0%,#a9acb8 45%,var(--purple-light) 70%,var(--purple) 100%)}
.service-card span{position:absolute;left:0;right:0;bottom:28px;text-align:center;font-family:"Poppins",sans-serif;font-weight:600;font-size:20px;color:var(--white)}

/* testimonials */
.testimonials{left:0;top:2020px;width:1200px;height:668px;background:var(--purple)}
.testimonial-box{left:112px;top:2136px;width:976px;height:447px;background:var(--white)}
.testimonials-title{left:170px;top:2180px;font-size:38px}
.client{left:147px;width:426px;height:74px;display:flex;align-items:center;padding-left:14px}
.client.active{background:var(--purple)}
.avatar{width:58px;height:58px;border-radius:50%;background:#c9c3cf;margin-right:24px}
.client.active .avatar{background:#e2dce8}
.client-name{font-weight:600;font-size:15px;color:var(--ink)}
.client-date{font-weight:400;font-size:12.5px;color:var(--ink)}
.client.active .client-name,.client.active .client-date{color:var(--white)}
.quote-mark{font-family:"Jost",sans-serif;font-weight:700;font-size:64px;color:var(--purple);line-height:1}
.quote-copy{left:624px;top:2270px;width:412px;font-size:15.5px;line-height:30px;text-align:justify}

/* blog */
.blog{left:0;top:2688px;width:1200px;height:663px;background:linear-gradient(135deg,#f7f7f9,#eeeef2 50%,#f6f6f8)}
.blog-title{left:0;width:1200px;top:2778px;text-align:center;font-size:40px}
.blog-photo{top:2881px;width:268px;height:170px;box-shadow:0 3px 8px rgba(0,0,0,.15)}
.blog-name{top:3072px;font-family:"Poppins",sans-serif;font-weight:600;font-size:16px;color:#333}
.blog-copy{top:3108px;width:234px;font-weight:300;font-size:15.5px;line-height:25px;color:var(--text);text-align:justify}
.blog-more{top:3203px;font-weight:600;font-size:14.5px;color:#333}
.dot{top:3278px;width:8px;height:8px;border-radius:50%;background:#c8b8d8}

/* schedule */
.schedule-strip{left:1088px;top:3351px;width:112px;height:687px;background:var(--purple)}
.schedule-title{left:134px;top:3438px;font-size:36px;letter-spacing:.3px}
.schedule-copy{left:134px;top:3505px;width:480px}
.field-label{left:134px;font-weight:400;font-size:16.5px;color:var(--text)}
.field-line{left:134px;width:466px;height:1.5px;background:#444}
.send-btn{left:134px;top:3893px;width:164px;height:55px}
.info-accent{left:741px;top:3497px;width:62px;height:59px;background:var(--purple)}
.info-box{left:756px;top:3517px;width:380px;height:353px;background:#000}
.info-title{left:814px;top:3568px;font-family:"Poppins",sans-serif;font-weight:600;font-size:22px;color:var(--white)}
.info-item{left:814px;display:flex;align-items:center;gap:18px;font-weight:500;font-size:16.5px;color:var(--white)}
.info-item svg{width:16px;height:16px}

/* footer */
.footer{left:0;top:4038px;width:1200px;height:271px;background:#111}
.footer-brand{left:118px;top:4140px;font-family:"Poppins",sans-serif;font-weight:600;font-size:22px;color:var(--white);letter-spacing:2px;display:flex;align-items:center;gap:10px}
.footer-brand .brand-dot{width:20px;height:20px;background:var(--white)}
.footer-copy{left:114px;top:4196px;width:260px;font-weight:400;font-size:15.5px;line-height:25px;color:var(--white)}
.footer-link{top:4100px;font-weight:500;font-size:16.5px;color:var(--white);letter-spacing:.5px}
.social{top:4156px;width:16px;height:16px;border-radius:50%;background:var(--white)}
.legal{left:0;top:4309px;width:1200px;height:55px;background:#000}
.legal span{position:absolute;left:112px;top:17px;font-size:14.5px;color:var(--white)}
</style>
</head>
<body>

<header class="abs site-nav">
  <div class="abs brand" style="top:22px;left:118px"><span class="brand-dot"></span>BRENLOW</div>
  <a class="abs nav-link" style="left:352px">HOME</a>
  <a class="abs nav-link" style="left:483px">ABOUT US</a>
  <a class="abs nav-link" style="left:653px">SERVICE</a>
  <a class="abs nav-link" style="left:802px">TESTIMONIAL</a>
  <a class="abs nav-link" style="left:997px">CONTACT</a>
</header>

<section class="abs hero"></section>
<div class="abs hero-photo" role="img" aria-label="Businesswoman with a tablet talking to a senior doctor in scrubs"></div>
<h1 class="abs hero-title">WELCOME TO<br>BRENLOW</h1>
<p class="abs hero-copy">Sed ut perspiciatis unde omnis iste natus error sit voluptatem accusantium doloremque laudantium, totam rem aperiam, eaque ipsa quae ab illo inventore veritatis et quasi architecto</p>

<div class="abs about-photo" role="img" aria-label="Hand holding a magnifying glass over a medical cross surrounded by wooden health icon discs"></div>
<h2 class="abs heading about-title">About Us</h2>
<p class="abs body-copy about-copy">Lorem ipsum dolor sit amet, consectetur adipiscing elit, sed do eiusmod tempor incididunt ut labore et dolore magna aliqua. Ut enim ad minim veniam, quis nostrud exercitation ullamco laboris nisi ut aliquip ex ea commodo consequat. Duis aute irure dolor in reprehenderit in voluptate velit esse cillum dolore eu fugiat nulla pariatur. Excepteur sint occaecat cupidatat non proident, sunt in culpa qui officia deserunt mollit anim id est laborum.</p>
<a class="abs btn about-btn">READ MORE</a>

<section class="abs services"></section>
<h2 class="abs heading services-title">Services</h2>
<p class="abs body-copy services-copy">Lorem ipsum dolor sit amet, consectetur adipiscing elit, sed do eiusmod tempor incididunt ut labore et dolore magna aliqua. Ut enim ad minim veniam, quis nostrud exercitation ullamco laboris nisi ut aliquip ex ea commodo consequat.</p>
<div class="abs service-card" style="left:190px" role="img" aria-label="Pharmacist talking with a smiling senior woman"><span>LOREM IPSUM</span></div>
<div class="abs service-card" style="left:470px" role="img" aria-label="Businessman and nurse reviewing a clipboard"><span>LOREM IPSUM</span></div>
<div class="abs service-card" style="left:748px" role="img" aria-label="Doctor reading a tablet in a hospital corridor"><span>LOREM IPSUM</span></div>

<section class="abs testimonials"></section>
<div class="abs testimonial-box"></div>
<h2 class="abs heading testimonials-title">Testimonials</h2>
<div class="abs client" style="top:2268px"><div class="avatar" role="img" aria-label="Client portrait"></div><div><div class="client-name">LOREM IPSUM DOLOR</div><div class="client-date">18th May 2023</div></div></div>
<div class="abs client active" style="top:2370px"><div class="avatar" role="img" aria-label="Client portrait"></div><div><div class="client-name">LOREM IPSUM DOLOR</div><div class="client-date">18th May 2023</div></div></div>
<div class="abs client" style="top:2456px"><div class="avatar" role="img" aria-label="Client portrait"></div><div><div class="client-name">LOREM IPSUM DOLOR</div><div class="client-date">18th May 2023</div></div></div>
<div class="abs quote-mark" style="left:598px;top:2216px">&ldquo;</div>
<p class="abs body-copy quote-copy">Lorem ipsum dolor sit amet, consectetur adipiscing elit, sed do eiusmod tempor incididunt ut labore et dolore magna aliqua. Ut enim ad minim veniam, quis nostrud exercitation ullamco laboris nisi ut aliquip ex ea commodo consequat. Duis aute irure dolor in reprehenderit in voluptate velit</p>
<div class="abs quote-mark" style="left:996px;top:2456px">&rdquo;</div>

<section class="abs blog"></section>
<h2 class="abs heading blog-title">Blog</h2>
<div class="abs blog-photo" style="left:144px;background:linear-gradient(135deg,#dfe3ea,#5b7fb8)" role="img" aria-label="Businessman and medical staff reviewing a tablet"></div>
<div class="abs blog-photo" style="left:466px;background:linear-gradient(135deg,#bcd7ee,#6f9cc9)" role="img" aria-label="Doctor using a holographic medical interface over a laptop"></div>
<div class="abs blog-photo" style="left:785px;background:linear-gradient(135deg,#cfd6de,#40627e)" role="img" aria-label="Two medical professionals in scrubs reviewing a tablet"></div>
<h3 class="abs blog-name" style="left:158px">LOREM IPSUM DOLOR</h3>
<h3 class="abs blog-name" style="left:479px">LOREM IPSUM DOLOR</h3>
<h3 class="abs blog-name" style="left:801px">LOREM IPSUM DOLOR</h3>
<p class="abs blog-copy" style="left:156px">Sed ut perspiciatis unde omnis iste natus error sit voluptatem accusantium</p>
<p class="abs blog-copy" style="left:477px">Sed ut perspiciatis unde omnis iste natus error sit voluptatem accusantium</p>
<p class="abs blog-copy" style="left:799px">Sed ut perspiciatis unde omnis iste natus error sit voluptatem accusantium</p>
<a class="abs blog-more" style="left:156px">READ MORE</a>
<a class="abs blog-more" style="left:477px">READ MORE</a>
<a class="abs blog-more" style="left:799px">READ MORE</a>
<span class="abs dot" style="left:601px"></span>
<span class="abs dot" style="left:612px;background:var(--purple)"></span>
<span class="abs dot" style="left:623px"></span>

<div class="abs schedule-strip"></div>
<h2 class="abs heading schedule-title">Schedule a 15 Minutes Call</h2>
<p class="abs body-copy schedule-copy">Lorem ipsum dolor sit amet, consectetur adipiscing elit, sed do eiusmod tempor incididunt ut labore et dolore magna aliqua.</p>
<label class="abs field-label" style="top:3652px">Name</label>
<div class="abs field-line" style="top:3689px"></div>
<label class="abs field-label" style="top:3720px">Email</label>
<div class="abs field-line" style="top:3758px"></div>
<label class="abs field-label" style="top:3789px">Message</label>
<div class="abs field-line" style="top:3826px"></div>
<a class="abs btn send-btn">SEND</a>

<div class="abs info-accent"></div>
<div class="abs info-box"></div>
<h3 class="abs info-title">INFO</h3>
<div class="abs info-item" style="top:3636px"><svg viewBox="0 0 16 16" fill="none" stroke="#fff" stroke-width="1.4"><rect x="1.5" y="3" width="13" height="10" rx="1"/><path d="M1.5 4l6.5 5 6.5-5"/></svg><span>hello@brenlowwealth.com</span></div>
<div class="abs info-item" style="top:3687px"><svg viewBox="0 0 16 16" fill="#fff"><path d="M3 1.5l2.5 0 1.2 3-1.6 1.2c.8 1.7 2 2.9 3.7 3.7l1.2-1.6 3 1.2v2.5c0 .8-.7 1.5-1.5 1.5C6.6 13 3 9.4 1.5 3c0-.8.7-1.5 1.5-1.5z"/></svg><span>+1 555 204 7316</span></div>
<div class="abs info-item" style="top:3734px"><svg viewBox="0 0 16 16" fill="#fff"><circle cx="8" cy="5" r="4"/><rect x="7.2" y="8" width="1.6" height="7"/></svg><span>location</span></div>
<div class="abs info-item" style="top:3781px"><svg viewBox="0 0 16 16" fill="none" stroke="#fff" stroke-width="1.4"><rect x="1.5" y="3" width="13" height="11.5"/><path d="M1.5 6.5h13M5 1v3M11 1v3M4 9h2M7 9h2M10 9h2M4 11.5h2M7 11.5h2"/></svg><span>05.00 - 06.00</span></div>

<footer class="abs footer"></footer>
<div class="abs footer-brand"><span class="brand-dot"></span>BRENLOW</div>
<p class="abs footer-copy">Sed ut perspiciatis unde omnis iste natus error sit voluptatem accusantium</p>
<a class="abs footer-link" style="left:361px">HOME</a>
<a class="abs footer-link" style="left:492px">ABOUT US</a>
<a class="abs footer-link" style="left:661px">SERVICE</a>
<a class="abs footer-link" style="left:810px">TESTIMONIAL</a>
<a class="abs footer-link" style="left:1005px">CONTACT</a>
<span class="abs social" style="left:887px"></span>
<span class="abs social" style="left:931px"></span>
<span class="abs social" style="left:966px"></span>
<span class="abs social" style="left:1013px"></span>
<span class="abs social" style="left:1064px"></span>
<div class="abs legal"><span>&copy; 2023 Brenlow</span></div>

</body>
</html>
```